Website for Swedish wellness company "Heartmeadow"

We need a website for our Swedish wellness company. The name is "Heartmeadow" . The company is all about sustainablility for our body, soul and planet. We work with coaching, yoga, massage, healthy food, retreats(sports, excercise, sufing), healing and inspirational talks. We are convinced that personal sustainability and a strong spiritual connection to yourself will lead to planetary sustainability. Our customers are both companies and consumers from all over the world. The final design should be clean/simple and you should get a feeling of community, happiness, warmth, connection,, joy, spirituality but still a professional touch.Just got a logo from Pixel Harbor and are very happy with it;-)
Updates

Sorry I was too enthusiastic posting this project. Of course I will give you some text as well för the different pages! I will see to that it is finished by friday so if you want to wait with your submissions please do! Best regards Maria

Target Market(s)

Businesses and consumers

Industry/Entity Type

Health And Wellness

Number of Pages Required

5+ page

Font styles to use
Sans Serif

Colors
33a6d7
00a990
b7a5cd

Requirements
Must have
• Idea about pages:
• I am not sure how many pages I get for the price, but 5 would be nice to start with.
• Not sure what write ups is;-)
• But title of the pages could be:
• Landing page
• About us
• Services
• Retreats
• Contact us
Nice to have
• A clean and professional website but with some heart and soul in it. Because we Would love colours that harmonize with our logo, but other ideas are welcome!

```html
<!DOCTYPE html>
<html lang="en">
<head>
<meta charset="utf-8">
<title>Heartmeadow – Wellness for Body, Soul and Planet</title>
<link href="https://fonts.googleapis.com/css2?family=Cinzel:wght@400;700&family=Roboto:ital,wght@0,400;0,500;0,700;1,400&display=swap" rel="stylesheet">
<style>
:root{
  --teal:#1a9b86;
  --teal-light:#5fc9bb;
  --navy:#0e2d5c;
  --navy-deep:#0a2350;
  --ink:#1c1c1c;
  --text:#555a60;
  --nav:#1e3562;
  --gold:#f3b51b;
  --paper:#ffffff;
  --mist:#f4f6f6;
  --serif:'Cinzel',serif;
  --sans:'Roboto',sans-serif;
}
*{box-sizing:border-box;margin:0;padding:0}
html,body{width:1200px;height:4468px;overflow:hidden}
body{position:relative;background:var(--paper);font-family:var(--sans);color:var(--text)}
.abs{position:absolute}
.serif-title{font-family:var(--serif);font-weight:400;color:var(--ink);letter-spacing:.5px}
.btn{position:absolute;display:flex;align-items:center;justify-content:center;gap:6px;background:var(--teal);color:#fff;font:500 16px var(--sans);border-radius:30px;text-transform:uppercase}
.btn .dot{width:13px;height:13px;border-radius:50%;background:#fff;position:relative}
.btn .dot::after{content:"";position:absolute;left:4px;top:3.5px;border-left:6px solid var(--teal);border-top:3px solid transparent;border-bottom:3px solid transparent}

/* header */
.site-header{position:absolute;left:0;top:0;width:1200px;height:173px;background:#fff;border-top:3px solid var(--teal)}
.brand{position:absolute;left:110px;top:62px;display:flex;align-items:center;gap:10px}
.brand-mark{width:40px;height:40px;border-radius:50%;background:var(--teal)}
.brand-name{font:700 24px var(--serif);color:var(--nav)}
.main-nav{position:absolute;top:76px;left:446px;display:flex;gap:38px;font:500 18px var(--sans);color:var(--nav)}
.main-nav .active{position:relative}
.main-nav .active::before,.main-nav .active::after{content:"";position:absolute;left:8px;width:40px;height:14px;border:2px solid var(--teal);border-radius:50%}
.main-nav .active::before{top:-18px;border-bottom:none;border-left-color:transparent;border-right-color:transparent}
.main-nav .active::after{bottom:-18px;border-top:none;border-left-color:transparent;border-right-color:transparent}
.search{position:absolute;left:1070px;top:79px}

/* hero */
.hero{position:absolute;left:0;top:173px;width:1200px;height:700px;background:linear-gradient(180deg,#8ea3b5 0%,#6f8693 35%,#3f5a4d 70%,#2f4a3a 100%)}
.hero-title{position:absolute;left:640px;top:220px;font:700 58px var(--serif);color:#fff;text-shadow:0 2px 6px rgba(0,0,0,.35)}
.hero-text{position:absolute;left:642px;top:305px;width:460px;font:400 18px/1.6 var(--sans);color:#fff}
.hero-btn{left:642px;top:396px;width:178px;height:48px}
.hero-scroll{position:absolute;left:584px;top:505px}

/* badges */
.badge{position:absolute;width:92px;height:92px;margin-left:-46px;margin-top:-46px;border-radius:50%;background:#fff;box-shadow:0 3px 10px rgba(0,0,0,.18);display:flex;align-items:center;justify-content:center}
.badge::after{content:"";width:62px;height:62px;border-radius:50%;border:3px solid var(--teal-light)}

/* about */
.about{position:absolute;left:0;top:850px;width:1200px;height:720px;background:linear-gradient(180deg,#fbfcfc,#f1f4f3)}
.about-title{position:absolute;left:111px;top:1000px;font-size:40px}
.about p{font:400 15.5px/1.85 var(--sans);color:var(--text);text-align:justify}
.about-copy{position:absolute;left:111px;top:1080px;width:470px}
.about-copy p+p{margin-top:20px}
.about-btn{left:111px;top:1374px;width:166px;height:46px}
.about-ring{position:absolute;left:643px;top:1002px;width:424px;height:424px;border-radius:50%;border:10px solid var(--teal-light);background:#fff;display:flex;align-items:center;justify-content:center}
.about-photo{width:378px;height:378px;border-radius:50%;background:linear-gradient(135deg,#b58a5d,#e9e2dc 55%,#3a4e86)}

/* services */
.services-title{position:absolute;left:0;width:1200px;top:1685px;text-align:center;font-size:42px;color:#fff}
.services-text{position:absolute;left:220px;width:760px;top:1762px;text-align:center;font:400 15.5px/1.85 var(--sans);color:#fff}
.service-card{position:absolute;top:1867px;width:219px;height:269px;box-shadow:0 4px 12px rgba(0,0,0,.35);display:flex;align-items:flex-end;justify-content:center;padding-bottom:28px}
.service-card span{font:700 21px var(--serif);color:#fff;text-shadow:0 2px 4px rgba(0,0,0,.6)}
.pager{position:absolute;left:525px;top:2200px;display:flex;gap:14px;align-items:center}
.pager i{width:13px;height:13px;border-radius:50%;border:2px solid #fff}
.pager i.on{background:#fff}
.pager .arrow{width:22px;height:22px;border-radius:50%;background:#fff;position:relative}

/* clients */
.clients{position:absolute;left:0;top:2330px;width:1200px;height:620px;background:linear-gradient(180deg,#f1f3f3,#fafbfb)}
.clients-title{position:absolute;left:0;width:1200px;top:2495px;text-align:center;font-size:42px}
.testimonial{position:absolute;top:2612px;width:470px;height:190px}
.t-photo{position:absolute;left:0;top:0;width:140px;height:168px;border-radius:50%;border:4px solid #fff;box-shadow:0 2px 8px rgba(0,0,0,.2)}
.t-quote{position:absolute;left:52px;top:150px;width:36px;height:36px;border-radius:50%;background:var(--teal);color:#fff;font:700 26px/44px Georgia,serif;text-align:center}
.t-body{position:absolute;left:156px;top:0;width:312px}
.stars{color:var(--gold);font-size:15px;letter-spacing:1px}
.t-body p{margin-top:12px;font:italic 400 14px/1.8 var(--sans);color:#6a6e72;text-align:justify}
.t-name{margin-top:10px;font:500 19px var(--sans);color:var(--nav)}
.side-arrow{position:absolute;top:2700px}

/* news */
.news-title{position:absolute;left:0;width:1200px;top:3097px;text-align:center;font-size:42px}
.news-card{position:absolute;top:3194px;height:491px;background:#fff;box-shadow:0 2px 10px rgba(0,0,0,.12)}
.news-img{height:243px}
.news-go{position:absolute;top:218px;width:52px;height:52px;border-radius:50%;background:var(--teal);display:flex;align-items:center;justify-content:center}
.news-body{padding:30px 38px 0 38px}
.news-body h3{font:500 21px/1.55 var(--sans);color:var(--nav)}
.meta{margin-top:14px;font:400 13.5px var(--sans);color:#7a7e82;display:flex;gap:14px;align-items:center}
.meta b{color:#4a8bc2;font-weight:400}
.news-body p{margin-top:18px;font:400 13.5px/1.95 var(--sans);color:#6a6e72;text-align:justify}
.news-btn{left:492px;top:3738px;width:215px;height:50px}

/* footer */
.footer-head{font:500 16px var(--sans);color:#fff;text-transform:uppercase}
.social{position:absolute;left:111px;top:4122px;display:flex;gap:24px}
.social i{width:22px;height:22px;border-radius:50%;background:#fff}
.social-line{position:absolute;left:111px;top:4168px;width:72px;height:2px;background:var(--teal)}
.foot-links{position:absolute;left:111px;top:4198px;list-style:none;font:400 15px/26.5px var(--sans);color:#fff}
.foot-links li::before{content:"»";margin-right:22px}
.newsletter{position:absolute;left:420px;width:360px;top:4120px;text-align:center}
.newsletter p{margin-top:24px;font:400 14px/1.7 var(--sans);color:#fff}
.field{position:absolute;left:456px;top:4241px;width:288px;height:42px;border:1.5px solid #4aa9a0;color:#fff;font:400 11px/40px var(--sans);text-align:center}
.subscribe{position:absolute;left:456px;top:4300px;width:288px;height:43px;background:var(--teal);color:#fff;font:500 16px/43px var(--sans);text-align:center}
.contact{position:absolute;left:848px;top:4120px}
.c-item{position:absolute;left:0;display:flex;gap:20px;align-items:center;font:400 14px/1.6 var(--sans);color:#fff;width:260px}
.c-icon{flex:none;width:34px;height:34px;border-radius:50%;background:#fff;display:flex;align-items:center;justify-content:center}
.copyright{position:absolute;left:0;width:1200px;top:4409px;text-align:center;font:400 15px var(--sans);color:#fff}
</style>
</head>
<body>

<header class="site-header">
  <div class="brand"><span class="brand-mark"></span><span class="brand-name">HEARTMEADOW</span></div>
  <nav class="main-nav">
    <span class="active">HOME</span><span>ABOUT US</span><span>SERVICES</span><span>RETREATS</span><span>CONTACT US</span>
  </nav>
  <svg class="search" width="18" height="18" viewBox="0 0 18 18"><circle cx="7" cy="7" r="5.5" fill="none" stroke="#1e3562" stroke-width="2.4"/><line x1="11" y1="11" x2="16" y2="16" stroke="#1e3562" stroke-width="2.6" stroke-linecap="round"/></svg>
</header>

<section class="hero" role="img" aria-label="Woman holding a yoga dancer pose on a mat above misty green mountains"></section>
<h1 class="hero-title">HEARTMEADOW</h1>
<p class="hero-text">Lorem ipsum dolor sit amet consectetur adipiscing elit sed do eiusmod dolor tempor.</p>
<div class="btn hero-btn">Read More <span class="dot"></span></div>
<svg class="hero-scroll" width="32" height="30" viewBox="0 0 32 30"><polyline points="3,3 16,14 29,3" fill="none" stroke="#fff" stroke-width="3.5"/><polyline points="3,15 16,26 29,15" fill="none" stroke="#fff" stroke-width="3.5"/></svg>

<section class="about" role="img" aria-label="Faint photo of a smiling woman behind the about section"></section>
<svg class="abs" style="left:0;top:700px" width="1200" height="200" viewBox="0 0 1200 200">
  <path d="M0,28 Q600,272 1200,28 L1200,200 L0,200 Z" fill="#fbfcfc"/>
  <path d="M0,36 Q600,280 1200,36" fill="none" stroke="#1a9b86" stroke-width="5"/>
</svg>
<div class="badge" style="left:600px;top:847px"></div>

<h2 class="serif-title about-title">ABOUT HEARTMEADOW</h2>
<div class="about about-copy" style="height:auto;background:none">
  <p>Lorem ipsum dolor sit amet, consectetur adipiscing elit, sed do eiusmod tempor incididunt ut labore et dolore magna aliqua.</p>
  <p>Ut enim ad minim veniam, quis nostrud exercitation ullamco laboris nisi ut aliquip ex ea commodo consequat. Duis aute irure dolor in reprehenderit in voluptate velit esse cillum dolore eu fugiat nulla pariatur. Excepteur sint occaecat cupidatat non proident, sunt in culpa qui officia deserunt mollit anim id est voluptate velit esse laborum.</p>
</div>
<div class="btn about-btn">Read More <span class="dot"></span></div>
<div class="about-ring"><div class="about-photo" role="img" aria-label="Therapist giving a seated back massage to a client"></div></div>

<svg class="abs" style="left:0;top:1540px" width="1200" height="820" viewBox="0 0 1200 820">
  <defs><linearGradient id="navyBand" x1="0" y1="0" x2="0" y2="1"><stop offset="0" stop-color="#0f2e5e"/><stop offset="1" stop-color="#0b2550"/></linearGradient></defs>
  <path d="M0,130 Q600,-100 1200,130 L1200,700 Q600,880 0,700 Z" fill="url(#navyBand)"/>
  <path d="M0,118 Q600,-112 1200,118" fill="none" stroke="#1a9b86" stroke-width="5"/>
  <path d="M0,712 Q600,892 1200,712" fill="none" stroke="#1a9b86" stroke-width="5"/>
</svg>
<div class="clients" role="img" aria-label="Faint photo of a woman relaxing during a massage" style="top:2370px;height:580px"></div>
<svg class="abs" style="left:0;top:2230px" width="1200" height="150" viewBox="0 0 1200 150">
  <path d="M0,10 Q600,190 1200,10 L1200,150 L0,150 Z" fill="#f1f3f3"/>
  <path d="M0,22 Q600,202 1200,22" fill="none" stroke="#1a9b86" stroke-width="5"/>
</svg>
<div class="badge" style="left:600px;top:1560px"></div>

<h2 class="serif-title services-title">OUR SERVICES</h2>
<p class="services-text">Lorem ipsum dolor sit amet, consectetur adipiscing elit sed do eiusmod tempor incididunt ut labore et dolore magna aliqua. Ut enim ad minim veniam quis nostrud exercitation.</p>
<div class="service-card" style="left:111px;background:linear-gradient(160deg,#d9c7a4,#8a6a4c 60%,#5a4433)" role="img" aria-label="Woman holding fresh green vegetables"><span>HEALTHY FOOD</span></div>
<div class="service-card" style="left:364px;background:linear-gradient(160deg,#6b3a1d,#c28a5e 55%,#4a2613)" role="img" aria-label="Woman relaxing with eyes closed during a massage"><span>MASSAGE</span></div>
<div class="service-card" style="left:617px;background:linear-gradient(180deg,#7a90b4,#d9a46a 55%,#2c3a58)" role="img" aria-label="Woman in a yoga lunge at sunset by the sea"><span>YOGA</span></div>
<div class="service-card" style="left:870px;background:linear-gradient(180deg,#3b3a9c,#c7479b 50%,#1d1b4a)" role="img" aria-label="Silhouette meditating under a glowing night sky"><span>HEALING</span></div>
<div class="pager">
  <svg width="22" height="22" viewBox="0 0 22 22"><circle cx="11" cy="11" r="11" fill="#fff"/><polyline points="12,6 7,11 12,16" fill="none" stroke="#0e2d5c" stroke-width="2.4"/><line x1="7" y1="11" x2="16" y2="11" stroke="#0e2d5c" stroke-width="2.4"/></svg>
  <i></i><i class="on"></i><i></i>
  <svg width="22" height="22" viewBox="0 0 22 22"><circle cx="11" cy="11" r="11" fill="#fff"/><polyline points="10,6 15,11 10,16" fill="none" stroke="#0e2d5c" stroke-width="2.4"/><line x1="6" y1="11" x2="15" y2="11" stroke="#0e2d5c" stroke-width="2.4"/></svg>
</div>
<div class="badge" style="left:600px;top:2358px"></div>

<h2 class="serif-title clients-title">WHAT OUR CLIENTS SAY</h2>
<svg class="side-arrow" style="left:40px" width="32" height="24" viewBox="0 0 32 24"><polyline points="12,2 2,12 12,22" fill="none" stroke="#3d8fd1" stroke-width="3"/><line x1="2" y1="12" x2="31" y2="12" stroke="#3d8fd1" stroke-width="3"/></svg>
<svg class="side-arrow" style="left:1128px" width="32" height="24" viewBox="0 0 32 24"><polyline points="20,2 30,12 20,22" fill="none" stroke="#3d8fd1" stroke-width="3"/><line x1="1" y1="12" x2="30" y2="12" stroke="#3d8fd1" stroke-width="3"/></svg>
<div class="testimonial" style="left:111px">
  <div class="t-photo" style="background:linear-gradient(150deg,#e7b07a,#a86a3c)" role="img" aria-label="Portrait of a smiling client"></div>
  <div class="t-quote">“</div>
  <div class="t-body">
    <div class="stars">★★★★★</div>
    <p>“ Lorem ipsum dolor sit amet, consectetur adipiscing elit, sed do eiusmod tempor incididunt ut labore et dolore magna aliqua. Ut enim ad minim veniam, quis nostrud exercitation ullamco laboris nisi commodo consequat. ”</p>
    <div class="t-name">- Owen Lindqvist</div>
  </div>
</div>
<div class="testimonial" style="left:620px">
  <div class="t-photo" style="background:linear-gradient(150deg,#c9d4e4,#6f86a8)" role="img" aria-label="Portrait of a client wearing glasses"></div>
  <div class="t-quote">“</div>
  <div class="t-body">
    <div class="stars">★★★★★</div>
    <p>“ Lorem ipsum dolor sit amet, consectetur adipiscing elit, sed do eiusmod tempor incididunt ut labore et dolore magna aliqua. Ut enim ad minim veniam, quis nostrud exercitation ullamco laboris nisi commodo consequat. ”</p>
    <div class="t-name">- Sara Holm</div>
  </div>
</div>
<svg class="abs" style="left:0;top:2880px" width="1200" height="120" viewBox="0 0 1200 120">
  <path d="M0,0 L1200,0 L1200,20 Q600,180 0,20 Z" fill="#fafbfb"/>
</svg>
<div class="badge" style="left:600px;top:2965px"></div>

<h2 class="serif-title news-title">LATEST NEWS</h2>
<article class="news-card" style="left:111px;width:572px">
  <div class="news-img" style="background:linear-gradient(135deg,#6d7a4a,#3f5a2a 45%,#8a8f92)" role="img" aria-label="Stone mortar with fresh herbs and oil bottles"></div>
  <div class="news-go" style="left:500px"><svg width="24" height="16" viewBox="0 0 24 16"><polyline points="15,2 22,8 15,14" fill="none" stroke="#fff" stroke-width="3"/><line x1="2" y1="8" x2="21" y2="8" stroke="#fff" stroke-width="3"/></svg></div>
  <div class="news-body">
    <h3>Lorem ipsum dolor sit amet consectetur adipiscing elit sed do eiusmod tempor incididunt?</h3>
    <div class="meta"><span><b>●</b> Erik Dahl</span>|<span><b>▦</b> 22 Apr 2019</span>|<span><b>◔</b> 35 Comments</span></div>
    <p>Lorem ipsum dolor sit amet, consectetur adipiscing elit, sed do eiusmod tempor incididunt ut labore et dolore magna aliqua. Ut enim ad minim veniam, quis nostrud exercitation ullamco laboris...</p>
  </div>
</article>
<article class="news-card" style="left:720px;width:369px">
  <div class="news-img" style="background:linear-gradient(135deg,#c9b5a8,#e07a5f 45%,#3d8fb5)" role="img" aria-label="Group resting in child's pose on yoga mats"></div>
  <div class="news-go" style="left:290px"><svg width="24" height="16" viewBox="0 0 24 16"><polyline points="15,2 22,8 15,14" fill="none" stroke="#fff" stroke-width="3"/><line x1="2" y1="8" x2="21" y2="8" stroke="#fff" stroke-width="3"/></svg></div>
  <div class="news-body" style="padding:30px 28px 0 28px">
    <h3>Lorem ipsum dolor sit amet do consectetur adipiscing</h3>
    <div class="meta"><span><b>●</b> Erik Dahl</span>|<span><b>▦</b> 22 Apr 2019.</span></div>
    <p>Lorem ipsum dolor sit amet, retycd consectetur adipiscing elit, sed detukbjxao eiusmod tempor incididunt ut labore et dolore...</p>
  </div>
</article>
<div class="btn news-btn">View All News <span class="dot"></span></div>

<svg class="abs" style="left:0;top:3895px" width="1200" height="573" viewBox="0 0 1200 573">
  <path d="M0,150 Q600,-80 1200,150 L1200,573 L0,573 Z" fill="#0b2550"/>
  <path d="M0,138 Q600,-92 1200,138" fill="none" stroke="#1a9b86" stroke-width="5"/>
</svg>
<div class="badge" style="left:600px;top:3922px"></div>

<svg class="abs" style="left:572px;top:4040px" width="56" height="52" viewBox="0 0 56 52" fill="none" stroke="#fff" stroke-width="2.5"><path d="M4,22 L28,4 L52,22 L52,48 L4,48 Z"/><path d="M4,22 L28,38 L52,22"/><rect x="14" y="12" width="28" height="20"/><line x1="19" y1="19" x2="37" y2="19"/><line x1="19" y1="25" x2="37" y2="25"/></svg>

<div class="social" aria-label="Social links"><i></i><i></i><i></i><i></i><i></i></div>
<div class="social-line"></div>
<ul class="foot-links">
  <li>Home</li><li>About</li><li>Services</li><li>Retreats</li><li>Testimonials</li><li>Contact</li>
</ul>

<div class="newsletter">
  <div class="footer-head">Newsletter Subscription</div>
  <p>Register your Email Address to get a more<br>Information about us</p>
</div>
<div class="field">Email Address *</div>
<div class="subscribe">SUBSCRIBE</div>

<div class="contact">
  <div class="footer-head">Contact Information</div>
  <div class="c-item" style="top:66px"><span class="c-icon"><svg width="12" height="16" viewBox="0 0 12 16"><path d="M6,0 A6,6 0 0 1 12,6 C12,10 6,16 6,16 C6,16 0,10 0,6 A6,6 0 0 1 6,0 Z" fill="#0b2550"/><circle cx="6" cy="6" r="2.2" fill="#fff"/></svg></span><span>48 Meadow Lane, Green Town,<br>Lake County, SE.</span></div>
  <div class="c-item" style="top:142px"><span class="c-icon"><svg width="14" height="14" viewBox="0 0 14 14"><path d="M3,0 L5.5,3.5 L4,5.5 Q5.5,8.5 8.5,10 L10.5,8.5 L14,11 L12,14 Q5,13 1,6 Q0,3 3,0 Z" fill="#0b2550"/></svg></span><span>(+46) 555 010 220</span></div>
  <div class="c-item" style="top:198px"><span class="c-icon"><svg width="16" height="12" viewBox="0 0 16 12"><rect width="16" height="12" fill="#0b2550"/><polyline points="0,0 8,7 16,0" fill="none" stroke="#fff" stroke-width="1.5"/></svg></span><span>info@heartmeadow.com</span></div>
</div>

<div class="copyright">Copyrights © 2019 Heartmeadow. All Rights Reserved &nbsp;&nbsp; | &nbsp;&nbsp; Privacy Policy.</div>

</body>
</html>
```